Need a vitamin/supplement label

Hi,
I need a vitamin label designing for a product that will be sold online.
The label needs to have the following information on the front:
1) B12
2) Methycobalamin
3) 1000mcg
4) 90 Lozenges
5) Sublingual
6) Dietary Supplement
7) Vegetarian
Numbers 1 and 2 need to standout the most because the product will only be sold online so visibility is key.
Use this design as an inspiration:
http://www.shopvelmara.com/Corvelle-Naturals-Methylcobalamin-5000mcg-Lozenges/dp/Q7742KXRTA/ref=sr_1_2?ie=UTF8&qid=1381433791&sr=8-2&keywords=b12
The label should come across as premium.
The brand name is 'Quarlen Nutra' and I haven't had a logo designed so there's some freedom when it comes to that. It needs to be simple and clean.
If you need any clarifications then let me know.
Online

```html
<!DOCTYPE html>
<html lang="en">
<head>
<meta charset="UTF-8">
<title>Quarlen Nutra B-12 Label</title>
<link href="https://fonts.googleapis.com/css2?family=Roboto:ital,wght@0,400;0,500;0,700;1,700&family=Roboto+Condensed:wght@700&family=Tinos&display=swap" rel="stylesheet">
<style>
  :root {
    --bg: #e9eaeb;
    --label: #ffffff;
    --green: #2fa86a;
    --green-soft: #5cc08a;
    --blue-deep: #1a7fc2;
    --blue-mid: #3a94d4;
    --blue-light: #93d0f0;
    --brand-blue: #2b6fae;
    --text-blue: #3b8fd0;
    --info-blue: #3a6a99;
    --stripe: #e6e8ea;
  }
  * { margin: 0; padding: 0; box-sizing: border-box; }
  html, body { width: 1200px; height: 960px; overflow: hidden; }
  body { background: var(--bg); font-family: "Roboto", sans-serif; }
  .canvas { position: relative; width: 1200px; height: 960px; }
  .label {
    position: absolute; left: 356px; top: 200px; width: 466px; height: 680px;
    background: var(--label); overflow: hidden;
  }
  .top-rule { position: absolute; left: 0; top: 6px; width: 100%; height: 9px; background: var(--green); }
  .brand-bar { position: absolute; left: 0; top: 97px; width: 90px; height: 26px; background: var(--green-soft); }
  .brand {
    position: absolute; left: 104px; top: 86px;
    display: flex; align-items: center; gap: 12px;
  }
  .brand-square { width: 18px; height: 18px; background: var(--brand-blue); }
  .brand-name {
    font-family: "Tinos", serif; font-size: 40px; color: var(--brand-blue); line-height: 1;
  }
  .brain-art {
    position: absolute; left: 292px; top: 135px; width: 170px; height: 140px;
    border-radius: 50%;
    background: radial-gradient(circle, #4a7fdc 0%, #3866c4 38%, #bcc6d6 60%, rgba(255,255,255,0) 72%);
  }
  .tagline {
    position: absolute; right: 172px; top: 237px; text-align: right;
    font-weight: 700; font-style: italic; font-size: 24px; line-height: 30px; color: var(--text-blue);
  }
  .hero-band {
    position: absolute; left: 0; top: 302px; width: 412px; height: 154px;
    background: linear-gradient(90deg, var(--blue-light) 0%, var(--blue-mid) 45%, var(--blue-deep) 100%);
    border-radius: 0 10px 18px 0;
    border-top: 9px solid var(--green);
  }
  .product-name {
    position: absolute; left: 124px; top: 6px;
    font-family: "Roboto Condensed", sans-serif; font-weight: 700; font-size: 132px;
    line-height: 1; color: #fff; letter-spacing: 1px;
  }
  .product-form {
    position: absolute; left: 78px; top: 114px;
    font-size: 25px; color: #fff; letter-spacing: 2px; text-transform: uppercase; font-weight: 500;
  }
  .stripe-fill {
    position: absolute; left: 0; top: 456px; width: 100%; height: 14px;
    background: repeating-linear-gradient(135deg, var(--stripe) 0 2px, transparent 2px 6px);
  }
  .features { position: absolute; left: 0; top: 487px; list-style: none; }
  .feature {
    position: relative; font-size: 28px; font-weight: 500; color: var(--text-blue);
    line-height: 37px; padding-left: 16px;
  }
  .feature::before {
    content: ""; position: absolute; left: 0; top: 15px; width: 7px; height: 7px; background: var(--green-soft);
  }
  .feature:nth-child(1) { margin-left: 98px; }
  .feature:nth-child(2) { margin-left: 116px; }
  .feature:nth-child(3) { margin-left: 135px; }
  .info-rule { position: absolute; left: 64px; top: 602px; width: 345px; height: 2px; background: var(--green); }
  .info {
    position: absolute; left: 92px; top: 616px;
    font-size: 22px; font-weight: 700; color: var(--info-blue); word-spacing: 2px;
  }
  .info .divider { margin: 0 14px; }
</style>
</head>
<body>
  <main class="canvas">
    <section class="label">
      <div class="top-rule"></div>
      <div class="brand-bar"></div>
      <div class="brand">
        <span class="brand-square"></span>
        <span class="brand-name">Quarlen Nutra</span>
      </div>
      <div class="brain-art" role="img" aria-label="Glowing blue brain illustration"></div>
      <p class="tagline">Supports Nerve Cells and<br>Brain Tissue</p>
      <div class="hero-band">
        <h1 class="product-name">B-12</h1>
        <p class="product-form">Methycobalamin</p>
      </div>
      <div class="stripe-fill"></div>
      <ul class="features">
        <li class="feature">Sublingual</li>
        <li class="feature">Dietary Supplement</li>
        <li class="feature">Vegetarian</li>
      </ul>
      <div class="info-rule"></div>
      <p class="info">1000mcg<span class="divider">I</span>90 Lozenges</p>
    </section>
  </main>
</body>
</html>
```